Association qui souhaite améliorer l'accès aux personnes en situation de handicap

Nous sommes une association qui a pour objectif d'améliorer l'accessibilité, augmenter l'offre des activités réalisables dans notre région touristique.
Nous souhaitons réaliser un site internet afin de pouvoir communiquer sur notre association. Nous avons déjà conçu notre flyer sur Plumotrix. Nous souhaiterions une base graphique se rapportant à celui-ci. C'est possible de tout retravailler mais nous souhaitons tout de même retrouver la charte graphique ou code couleur du flyer.
Il nous faudrait quelques pages:
- 1 page : Acceuil / Présentation (Home), Il y aurait le descriptif de l'association, avec ses objectifs à +/- moyen terme
- 1 page : Nos réalisations, celle-ci présenterait les éléments que nous avons réalisés avec des zones de textes et des images classées chronologiquement au fur et à mesure des nouveautés
- 1 page : Media, comme la précédente, mais ou on pourrait voir ou lire sur les divers médias qui parlent de nous
- 1 page : Evenements : c'est une page pour présenter divers activités que nous allons organiser
- 1 page : Contact qui indique comment nous contacter et avec la présentation des 5 ou 6 membres du comité
- 1 link donate : qui arrive sur un formulaire de donnée que l'on pourra faire évoluer sur un système de payement par la suite. Cette bannière doit se retrouver sur toutes les pages
Il est nécessaire que se design puisse être transféré sur une lecture sur téléphone mobile
Personnes en situation de handicap
Associatif

```html
<!DOCTYPE html>
<html lang="en">
<head>
<meta charset="utf-8">
<title>Openway Association</title>
<link rel="stylesheet" href="https://fonts.googleapis.com/css2?family=Oswald:wght@500;600;700&family=Montserrat:wght@400;500;600;700&display=swap">
<style>
:root{
  --red:#c4161c;
  --red-dark:#a30f15;
  --ink:#1f1f1f;
  --text:#2a2a2a;
  --muted:#555;
  --dark:#262626;
  --dark-2:#1b1b1b;
  --line:#dcdcdc;
  --paper:#ffffff;
  --foot:#f5f5f5;
  --head:'Oswald',sans-serif;
  --body:'Montserrat',sans-serif;
}
*{box-sizing:border-box;margin:0;padding:0}
html,body{width:1200px;height:4515px;overflow:hidden}
body{position:relative;background:var(--paper);font-family:var(--body);color:var(--text)}
.abs{position:absolute}
.h{font-family:var(--head);text-transform:uppercase;color:var(--ink);letter-spacing:.5px;line-height:1.1}
.red{color:var(--red)}
.arrow{display:inline-block;width:16px;height:12px;vertical-align:middle;margin-left:10px}
.dots{background-image:radial-gradient(circle,#333 1.6px,transparent 2px);background-size:12px 12px}

/* top bar */
.topbar{left:622px;top:0;width:578px;height:44px;background:var(--red);clip-path:polygon(22px 0,100% 0,100% 100%,0 100%);color:#fff;font-size:14px;display:flex;align-items:center;padding-left:36px;gap:12px}
.topbar b{font-weight:600}
.topbar .sep{opacity:.7}
.topbar .stay{margin-left:48px}
.sdot{width:11px;height:11px;border-radius:50%;background:#fff;display:inline-block}
.brand{display:flex;align-items:center;gap:10px;font-family:var(--body);font-weight:700;color:var(--ink);text-transform:uppercase;line-height:1.05}
.brand .mark{width:26px;height:26px;background:var(--red)}
.header-brand{left:91px;top:38px;font-size:21px}
.nav{left:583px;top:76px;display:flex;gap:0;font-size:14px;font-weight:600;color:var(--ink);text-transform:uppercase}
.nav span{position:absolute;white-space:nowrap}

/* hero */
.hero{left:0;top:126px;width:1200px;height:601px;clip-path:polygon(0 0,100% 0,100% 72%,0 100%);background:linear-gradient(90deg,#7b7a70 0%,#5c5b55 35%,#2e2e2e 60%,#1e1e1e 100%)}
.hero-shade{left:0;top:126px;width:1200px;height:601px;clip-path:polygon(0 0,100% 0,100% 72%,0 100%);background:linear-gradient(90deg,rgba(0,0,0,0) 40%,rgba(0,0,0,.55) 65%)}
.hero-title{left:682px;top:240px;color:#fff}
.hero-title .l1{font-size:56px;color:#fff}
.hero-title .l2{font-size:76px;color:#fff}
.hero-copy{left:683px;top:378px;width:430px;color:#fff;font-size:17px;line-height:30px}
.btn-red{background:var(--red);color:#fff;font-family:var(--head);font-weight:500;text-transform:uppercase;font-size:17px;display:flex;align-items:center;justify-content:center;letter-spacing:.4px}
.hero-btn{left:683px;top:503px;width:228px;height:52px}
.side-arrow{width:37px;height:91px;background:#1c1c1c;display:flex;align-items:center;justify-content:center}

/* welcome */
.welcome-title{left:91px;top:900px;font-size:46px;line-height:54px}
.welcome-copy{left:91px;top:1027px;width:520px;font-size:18px;line-height:30px;color:var(--text)}
.welcome-photo{left:682px;top:769px;width:425px;height:512px;background:linear-gradient(160deg,#d9d4cb,#8e8a84 55%,#4a5c78)}

/* achievements */
.band-dark{left:0;top:1375px;width:1200px;height:783px;background:linear-gradient(180deg,#2b2b2b,#232323)}
.sec-title{width:1200px;left:0;text-align:center;color:#fff;font-size:46px}
.sec-sub{width:1200px;left:0;text-align:center;color:#fff;font-size:18px;line-height:30px}
.ach-card{top:1619px;width:322px;height:338px;overflow:hidden}
.ach-card .photo{position:absolute;inset:0}
.ach-card .label{position:absolute;left:0;bottom:0;width:100%;height:65px;background:#fff;clip-path:polygon(34px 0,100% 0,100% 100%,0 100%);font-family:var(--head);font-size:19px;font-weight:600;text-transform:uppercase;display:flex;align-items:center;justify-content:center;color:var(--ink);padding-left:18px}
.ach-card.active .label{background:var(--red);color:#fff}
.ach-card .go{position:absolute;right:0;bottom:52px;width:51px;height:44px;background:var(--red);display:flex;align-items:center;justify-content:center}
.ach-card.active .go{background:var(--red-dark)}
.btn-outline-light{left:459px;top:2018px;width:282px;height:53px;border:2px solid #fff;color:#fff;font-family:var(--head);font-weight:500;text-transform:uppercase;font-size:17px;display:flex;align-items:center;justify-content:center}

/* media */
.media-title{left:91px;top:2228px;font-size:46px}
.media-btn{left:925px;top:2237px;width:180px;height:55px}
.media-copy{left:91px;top:2303px;width:560px;font-size:18px;line-height:30px}
.media-card{width:497px;height:257px;border:2px solid #e6e6e6;border-radius:6px;background:#fff}
.media-card .photo{position:absolute;left:12px;top:12px;width:165px;height:232px}
.media-card .t{position:absolute;left:186px;top:26px;font-family:var(--head);font-weight:600;font-size:18px;line-height:28px;text-transform:uppercase;color:var(--ink)}
.media-card .p{position:absolute;left:186px;top:96px;font-size:16px;line-height:30px;color:var(--text)}
.media-card .b{position:absolute;left:186px;top:178px;width:172px;height:43px;border:2px solid var(--red);color:var(--red);font-family:var(--head);font-weight:500;font-size:16px;text-transform:uppercase;display:flex;align-items:center;justify-content:center}

/* events */
.events-band{left:0;top:3027px;width:1200px;height:908px;background:linear-gradient(180deg,#2a2a2a,#1f1f1f);clip-path:polygon(0 16%,71% 0,100% 10%,100% 100%,0 100%)}
.event-card{top:3383px;width:322px;height:473px;background:#fff}
.event-card .photo{position:absolute;left:0;top:0;width:100%;height:224px}
.event-card .date{position:absolute;left:245px;top:17px;width:62px;height:68px;background:var(--red);color:#fff;text-align:center;font-family:var(--head);font-size:27px;line-height:40px;font-weight:500}
.event-card .date small{display:block;background:#fff;color:var(--ink);font-size:14px;line-height:22px;margin:0 6px;font-weight:600}
.event-card .by{position:absolute;left:26px;top:248px;font-size:14px;color:var(--text)}
.event-card .t{position:absolute;left:26px;top:272px;font-family:var(--head);font-weight:600;font-size:18px;line-height:28px;text-transform:uppercase;color:var(--ink)}
.event-card .p{position:absolute;left:26px;top:338px;font-size:16px;line-height:30px;color:var(--text)}
.event-card .more{position:absolute;left:26px;top:425px;font-family:var(--head);font-weight:500;font-size:16px;text-transform:uppercase;color:var(--red)}

/* donate */
.donate{left:93px;top:3947px;width:1014px;height:130px;background:linear-gradient(90deg,#a30f15,var(--red) 40%,#b5131a);clip-path:polygon(0 0,92% 0,100% 100%,4% 100%)}
.donate-text{left:184px;top:3975px;color:#fff;font-size:29px;line-height:42px}
.donate-text .big{font-size:33px}
.donate-rule{left:665px;top:3962px;width:2px;height:88px;background:rgba(255,255,255,.75)}
.donate-btn{left:799px;top:3989px;width:215px;height:60px;background:#141414;color:#fff;font-family:var(--head);font-weight:500;font-size:17px;text-transform:uppercase;display:flex;align-items:center;justify-content:center}

/* footer */
.footer{left:0;top:4085px;width:1200px;height:430px;background:var(--foot)}
.footer-brand{left:91px;top:4186px;font-size:22px}
.soc{top:4271px;width:44px;height:44px;border:2px solid #333;border-radius:6px;display:flex;align-items:center;justify-content:center}
.soc i{width:12px;height:12px;background:#333;border-radius:2px}
.fcol-title{top:4166px;font-size:22px;font-weight:600}
.flinks{top:4208px;font-size:15px;line-height:32.5px;color:var(--ink)}
.cicon{width:46px;height:46px;border-radius:50%;background:var(--red);display:flex;align-items:center;justify-content:center}
.ctext{font-size:15px;line-height:26px;color:var(--ink)}
.frule{left:91px;top:4415px;width:1016px;height:1px;background:var(--line)}
.copy{left:0;top:4433px;width:1200px;text-align:center;font-size:14px;color:var(--muted)}
</style>
</head>
<body>

<!-- header -->
<div class="abs topbar">
  <svg width="18" height="18" viewBox="0 0 24 24" fill="none" stroke="#fff" stroke-width="2"><path d="M5 3h4l2 5-3 2a12 12 0 0 0 6 6l2-3 5 2v4a2 2 0 0 1-2 2A17 17 0 0 1 3 5a2 2 0 0 1 2-2z"/></svg>
  <span class="sep">|</span>
  <span>Call Us: <b>000-555-0142</b></span>
  <span class="stay">Stay with us:</span>
  <span class="sdot" aria-label="Social link"></span>
  <span class="sdot" aria-label="Social link"></span>
  <span class="sdot" aria-label="Social link"></span>
</div>
<div class="abs brand header-brand"><span class="mark"></span><span>Openway<br>Association</span></div>
<nav class="abs nav">
  <span style="left:0">Home</span>
  <span style="left:81px">Our Achievements</span>
  <span style="left:272px">Media</span>
  <span style="left:356px">Events</span>
  <span style="left:449px">Contact</span>
</nav>

<!-- hero -->
<div class="abs hero" role="img" aria-label="Photo of a helper guiding a person in a tracked wheelchair up outdoor steps"></div>
<div class="abs hero-shade"></div>
<div class="abs side-arrow" style="left:0;top:277px"><svg width="14" height="20" viewBox="0 0 14 20" fill="none" stroke="#fff" stroke-width="2.5"><path d="M11 2 3 10l8 8"/></svg></div>
<div class="abs side-arrow" style="left:1163px;top:277px"><svg width="14" height="20" viewBox="0 0 14 20" fill="none" stroke="#fff" stroke-width="2.5"><path d="M3 2l8 8-8 8"/></svg></div>
<h1 class="abs h hero-title"><span class="l1">Rejoin the</span><br><span class="l2">Association</span></h1>
<p class="abs hero-copy">Friends living in the region who are committed to making the Hautes Crêtes region as accessible as possible to people with disabilities.</p>
<a class="abs btn-red hero-btn">Contact us now <svg class="arrow" viewBox="0 0 16 12" fill="none" stroke="#fff" stroke-width="2"><path d="M1 6h13M9 1l5 5-5 5"/></svg></a>

<!-- welcome -->
<div class="abs dots" style="left:986px;top:710px;width:205px;height:126px"></div>
<h2 class="abs h welcome-title">Welcome to<br>Openway <span class="red">Association</span></h2>
<p class="abs welcome-copy">Lorem ipsum dolor sit ameti consectetur adipisicing elit sed do eiusmod tempor incididunt ut labore et doloreu magna aliqua. Ut enim ad minim veniam, quis nostrud exercitation ullamco laboris nisi ut aliquip ex ea comon consequat. Duis aute irure dolor in reprehenderit. Ut ito enim ad minim veniam, quis nostrud exercitation.</p>
<div class="abs welcome-photo" role="img" aria-label="Photo of a caregiver helping a woman with crutches stand up"></div>

<!-- achievements -->
<div class="abs band-dark"></div>
<h2 class="abs h sec-title" style="top:1448px">Our Achievements</h2>
<p class="abs sec-sub" style="top:1513px">Lorem ipsum dolor sit ameti consectetur adipisicing elit<br>sed do eiusmod tempor incididunt ut labore et</p>
<svg class="abs" style="left:21px;top:1777px" width="49" height="20" viewBox="0 0 49 20" fill="none" stroke="#fff" stroke-width="2"><path d="M48 10H2M11 2 2 10l9 8"/></svg>
<svg class="abs" style="left:1131px;top:1777px" width="49" height="20" viewBox="0 0 49 20" fill="none" stroke="#fff" stroke-width="2"><path d="M1 10h46M38 2l9 8-9 8"/></svg>

<div class="abs ach-card" style="left:93px">
  <div class="photo" role="img" aria-label="Photo of a smiling man in a cap and sunglasses outdoors" style="background:linear-gradient(170deg,#8fa07a,#c9a98a 50%,#d86a3e)"></div>
  <div class="label">Lorem ipsum dolar sit</div>
  <div class="go"><svg width="16" height="14" viewBox="0 0 16 14" fill="none" stroke="#fff" stroke-width="2"><path d="M1 7h13M9 2l5 5-5 5"/></svg></div>
</div>
<div class="abs ach-card active" style="left:440px">
  <div class="photo" role="img" aria-label="Photo of a smiling boy in a classroom" style="background:linear-gradient(170deg,#c9a06a,#9aa6b8 55%,#7c8aa0)"></div>
  <div class="label">Lorem ipsum dolar sit</div>
  <div class="go"><svg width="16" height="14" viewBox="0 0 16 14" fill="none" stroke="#fff" stroke-width="2"><path d="M1 7h13M9 2l5 5-5 5"/></svg></div>
</div>
<div class="abs ach-card" style="left:787px">
  <div class="photo" role="img" aria-label="Photo of a smiling older woman in a wheelchair" style="background:linear-gradient(170deg,#d8d4cf,#b7c4d2 55%,#9fb7cf)"></div>
  <div class="label">Lorem ipsum dolar sit</div>
  <div class="go"><svg width="16" height="14" viewBox="0 0 16 14" fill="none" stroke="#fff" stroke-width="2"><path d="M1 7h13M9 2l5 5-5 5"/></svg></div>
</div>
<a class="abs btn-outline-light">View all achievements <svg class="arrow" viewBox="0 0 16 12" fill="none" stroke="#fff" stroke-width="2"><path d="M1 6h13M9 1l5 5-5 5"/></svg></a>

<!-- media -->
<div class="abs dots" style="left:9px;top:2164px;width:48px;height:122px"></div>
<h2 class="abs h media-title">Our <span class="red">Media</span></h2>
<a class="abs btn-red media-btn">View more <svg class="arrow" viewBox="0 0 16 12" fill="none" stroke="#fff" stroke-width="2"><path d="M1 6h13M9 1l5 5-5 5"/></svg></a>
<p class="abs media-copy">Lorem ipsum dolor sit ameti consectetur adipisicing elit<br>sed do eiusmod tempor incididunt ut labore et</p>

<div class="abs dots" style="left:1023px;top:2780px;width:128px;height:205px"></div>

<div class="abs media-card" style="left:93px;top:2412px">
  <div class="photo" role="img" aria-label="Photo of a woman with a white cane in a park" style="background:linear-gradient(160deg,#6f7d5a,#c07a3a 60%,#8a6a4a)"></div>
  <div class="t">Sed ut perspiciatis under a<br>omnis iste natus error to</div>
  <div class="p">Lorem ipsum dolor sit ameti top<br>sed consectetur adipisicing elit</div>
  <div class="b">View more <svg class="arrow" viewBox="0 0 16 12" fill="none" stroke="#c4161c" stroke-width="2"><path d="M1 6h13M9 1l5 5-5 5"/></svg></div>
</div>
<div class="abs media-card" style="left:608px;top:2412px">
  <div class="photo" role="img" aria-label="Photo of a young girl smiling at a table" style="background:linear-gradient(160deg,#c9b9a6,#e8d8cc 55%,#b79d8a)"></div>
  <div class="t">Sed ut perspiciatis under a<br>omnis iste natus error to</div>
  <div class="p">Lorem ipsum dolor sit ameti top<br>sed consectetur adipisicing elit</div>
  <div class="b">View more <svg class="arrow" viewBox="0 0 16 12" fill="none" stroke="#c4161c" stroke-width="2"><path d="M1 6h13M9 1l5 5-5 5"/></svg></div>
</div>
<div class="abs media-card" style="left:93px;top:2686px">
  <div class="photo" role="img" aria-label="Photo of two hands holding each other" style="background:linear-gradient(160deg,#9aa7b5,#d7a68a 55%,#8a7a74)"></div>
  <div class="t">Sed ut perspiciatis under a<br>omnis iste natus error to</div>
  <div class="p">Lorem ipsum dolor sit ameti top<br>sed consectetur adipisicing elit</div>
  <div class="b">View more <svg class="arrow" viewBox="0 0 16 12" fill="none" stroke="#c4161c" stroke-width="2"><path d="M1 6h13M9 1l5 5-5 5"/></svg></div>
</div>
<div class="abs media-card" style="left:608px;top:2686px">
  <div class="photo" role="img" aria-label="Photo of an older woman with glasses in a wheelchair" style="background:linear-gradient(160deg,#b9c0c8,#8e9fb2 55%,#4d5e78)"></div>
  <div class="t">Sed ut perspiciatis under a<br>omnis iste natus error to</div>
  <div class="p">Lorem ipsum dolor sit ameti top<br>sed consectetur adipisicing elit</div>
  <div class="b">View more <svg class="arrow" viewBox="0 0 16 12" fill="none" stroke="#c4161c" stroke-width="2"><path d="M1 6h13M9 1l5 5-5 5"/></svg></div>
</div>

<!-- events -->
<div class="abs events-band"></div>
<h2 class="abs h sec-title" style="top:3212px">Latest Events</h2>
<p class="abs sec-sub" style="top:3274px">Lorem ipsum dolor sit ameti consectetur adipisicing elit<br>sed do eiusmod tempor incididunt ut labore et</p>
<svg class="abs" style="left:18px;top:3485px" width="49" height="20" viewBox="0 0 49 20" fill="none" stroke="#fff" stroke-width="2"><path d="M48 10H2M11 2 2 10l9 8"/></svg>
<svg class="abs" style="left:1133px;top:3485px" width="49" height="20" viewBox="0 0 49 20" fill="none" stroke="#fff" stroke-width="2"><path d="M1 10h46M38 2l9 8-9 8"/></svg>

<div class="abs event-card" style="left:93px">
  <div class="photo" role="img" aria-label="Photo of a woman in a wheelchair on a city street" style="background:linear-gradient(170deg,#2c3a5a,#7a8fa8 55%,#c9cdd3)"></div>
  <div class="date">24<small>MAR</small></div>
  <div class="by">Event By Maren Holt</div>
  <div class="t">Sed ut perspiciatis under a<br>omnis iste natus error to</div>
  <div class="p">Lorem ipsum dolor sit ameti top<br>sed consectetur adipisicing elit</div>
  <div class="more">View more <svg class="arrow" viewBox="0 0 16 12" fill="none" stroke="#c4161c" stroke-width="2"><path d="M1 6h13M9 1l5 5-5 5"/></svg></div>
</div>
<div class="abs event-card" style="left:440px">
  <div class="photo" role="img" aria-label="Photo of a man with sunglasses and a white cane in a park" style="background:linear-gradient(170deg,#9fb07a,#5d6b45 55%,#3a3a36)"></div>
  <div class="date">03<small>MAY</small></div>
  <div class="by">Event By Maren Holt</div>
  <div class="t">Sed ut perspiciatis under a<br>omnis iste natus error to</div>
  <div class="p">Lorem ipsum dolor sit ameti top<br>sed consectetur adipisicing elit</div>
  <div class="more">View more <svg class="arrow" viewBox="0 0 16 12" fill="none" stroke="#c4161c" stroke-width="2"><path d="M1 6h13M9 1l5 5-5 5"/></svg></div>
</div>
<div class="abs event-card" style="left:787px">
  <div class="photo" role="img" aria-label="Photo of a smiling boy by a window" style="background:linear-gradient(170deg,#8a8a7e,#a8845c 55%,#6a4a2e)"></div>
  <div class="date">12<small>JUN</small></div>
  <div class="by">Event By Maren Holt</div>
  <div class="t">Sed ut perspiciatis under a<br>omnis iste natus error to</div>
  <div class="p">Lorem ipsum dolor sit ameti top<br>sed consectetur adipisicing elit</div>
  <div class="more">View more <svg class="arrow" viewBox="0 0 16 12" fill="none" stroke="#c4161c" stroke-width="2"><path d="M1 6h13M9 1l5 5-5 5"/></svg></div>
</div>

<!-- footer -->
<div class="abs footer"></div>
<div class="abs dots" style="left:6px;top:4012px;width:64px;height:128px;opacity:.35"></div>
<div class="abs dots" style="left:1140px;top:4340px;width:52px;height:160px;opacity:.35"></div>

<!-- donate banner -->
<div class="abs donate"></div>
<h2 class="abs h donate-text"><span>Need help to</span><br><span class="big">Improve accessibility</span></h2>
<div class="abs donate-rule"></div>
<a class="abs donate-btn">Donate us now <svg class="arrow" viewBox="0 0 16 12" fill="none" stroke="#fff" stroke-width="2"><path d="M1 6h13M9 1l5 5-5 5"/></svg></a>

<div class="abs brand footer-brand"><span class="mark"></span><span>Openway<br>Association</span></div>
<div class="abs soc" style="left:93px" aria-label="Social link"><i></i></div>
<div class="abs soc" style="left:149px" aria-label="Social link"><i></i></div>
<div class="abs soc" style="left:205px" aria-label="Social link"><i></i></div>

<h3 class="abs h fcol-title" style="left:441px">Quick Links</h3>
<ul class="abs flinks" style="left:441px;list-style:none"><li>Home</li><li>Our Achievements</li><li>Media</li><li>Events</li></ul>
<h3 class="abs h fcol-title" style="left:671px">Other Links</h3>
<ul class="abs flinks" style="left:671px;list-style:none"><li>Privacy Policy</li><li>Terms &amp; Condition</li><li>FAQ</li><li>Contact</li></ul>
<h3 class="abs h fcol-title" style="left:900px">Contact Info</h3>
<div class="abs cicon" style="left:900px;top:4214px"><svg width="20" height="22" viewBox="0 0 24 24" fill="none" stroke="#fff" stroke-width="2"><path d="M12 22s7-7 7-12a7 7 0 0 0-14 0c0 5 7 12 7 12z"/><circle cx="12" cy="10" r="2.5"/></svg></div>
<p class="abs ctext" style="left:960px;top:4209px">Chemin des Sources 12<br>1870 Montclair</p>
<div class="abs cicon" style="left:900px;top:4282px"><svg width="20" height="20" viewBox="0 0 24 24" fill="none" stroke="#fff" stroke-width="2"><path d="M5 3h4l2 5-3 2a12 12 0 0 0 6 6l2-3 5 2v4a2 2 0 0 1-2 2A17 17 0 0 1 3 5a2 2 0 0 1 2-2z"/></svg></div>
<p class="abs ctext" style="left:960px;top:4277px">Phone:<br>000-555-0142</p>

<div class="abs frule"></div>
<p class="abs copy">Copyright © 2022 Openway Association. All rights reserved.</p>

</body>
</html>
```